Website for Ashcombe Tube Drift

Require a website for a river float in the City of Edmonton. Located on North Saskatchewan River. Will need to be a coded website with incorporated booking system through Fare Harbor software.

Pages include
Home
Pricing
About
FAQ
Contact

Ashcombe Tube Drift is an activity based business that will have customers floating down the North Saskatchewan river in Edmonton AB. The site will have all information needed and a full reservation system. The project was launched to provide people in the Edmonton area a favorite summer activity.

Here are similar websites to reference what our business will be doing and what we are looking for.

mossbankfloatco.com
quillpointpaddles.com

Target Market(s)

Families, Groups, Individuals, Anyone who wants to explore the river

Industry/Entity Type

Activities based business/ Outdoor recreational/ River Float

Coding

Coded - Design and coding required

Number of Pages Required

5+ page

Colors
0054AA
0677BA
7BADD7
CADEEF
E8F1F8
F0912C
F2A743
F7CA91
FBE8D2
FDF5EE

```html
<!DOCTYPE html>
<html lang="en">
<head>
<meta charset="utf-8">
<title>Ashcombe Tube Drift</title>
<link href="https://fonts.googleapis.com/css2?family=Archivo+Black&family=Montserrat:wght@400;500;600;700&family=Open+Sans:wght@400;600&display=swap" rel="stylesheet">
<style>
:root{
  --blue:#0054AA;--blue-2:#0677BA;--blue-3:#7BADD7;--blue-4:#CADEEF;--blue-5:#E8F1F8;
  --orange:#F0912C;--orange-2:#F2A743;--orange-3:#F7CA91;--orange-4:#FBE8D2;--orange-5:#FDF5EE;
  --ink:#1d1d2b;--text:#555;--white:#fff;
  --placeholder-a:#a9bccd;--placeholder-b:#c3cbd2;
}
*{margin:0;padding:0;box-sizing:border-box}
html,body{width:1200px;height:3806px;overflow:hidden}
body{font-family:"Montserrat",sans-serif;color:var(--ink);position:relative;background:var(--white)}
section,footer,header{position:absolute;left:0;width:1200px}
.abs{position:absolute}
.display{font-family:"Archivo Black",sans-serif;letter-spacing:.5px}
.btn{position:absolute;display:flex;align-items:center;justify-content:center;background:var(--orange);color:var(--white);font-weight:600;border-radius:6px;text-transform:uppercase}

/* hero */
.hero{top:0;height:615px;overflow:hidden}
.hero-photo{position:absolute;inset:0;background:linear-gradient(180deg,var(--placeholder-a) 0%,var(--placeholder-b) 100%)}
.logo{left:106px;top:18px;width:180px;height:140px;display:flex;flex-direction:column;align-items:center}
.logo-mark{width:88px;height:88px;border-radius:50%;background:var(--blue)}
.logo-name{margin-top:10px;font-weight:700;font-size:15px;color:var(--blue);white-space:nowrap}
.nav a{position:absolute;font-size:16px;font-weight:500;color:var(--ink);text-decoration:none;white-space:nowrap}
.nav a.active{border-bottom:3px solid var(--orange);padding-bottom:4px}
.hero-title{left:622px;top:190px;font-size:37px;line-height:52px;color:var(--ink)}
.hero .btn{left:622px;top:411px;width:127px;height:38px;font-size:14px}
.arrow{position:absolute;top:533px;width:40px;height:40px;border-radius:50%;background:var(--white);display:flex;align-items:center;justify-content:center}

/* pricing */
.pricing{top:615px;height:709px;background:var(--blue);color:var(--white)}
.pricing-photo{left:111px;top:104px;width:508px;height:508px;border-radius:50%;border:5px solid var(--white);background:var(--placeholder-b)}
.price-badge{left:108px;top:90px;width:210px;height:210px;border-radius:50%;background:var(--orange);border:6px solid var(--blue);display:flex;flex-direction:column;align-items:center;justify-content:center;text-align:center;font-family:"Open Sans",sans-serif;font-size:20px;line-height:26px}
.price-badge span{margin-top:18px;background:var(--blue);font-family:"Montserrat",sans-serif;font-size:11px;font-weight:600;padding:8px 16px;border-radius:5px}
.pricing h2{left:655px;top:90px;font-size:34px}
.pricing .lead{left:655px;top:156px;font-size:25px;line-height:35px;font-weight:600;width:470px}
.includes{left:655px;top:246px;list-style:none}
.includes li{height:34.3px;font-size:14.5px;font-weight:500;display:flex;align-items:center}
.includes li::before{content:"";width:9px;height:9px;border:2.5px solid var(--white);border-radius:50%;margin-right:14px}
.book-link{left:655px;top:533px;font-size:14.5px;font-weight:600;text-decoration:underline;color:var(--white)}
.group{left:655px;top:570px;font-size:26px;font-weight:600}
.pricing .btn{left:935px;top:566px;width:127px;height:42px;font-size:13px}
.note{left:659px;top:610px;font-size:13px;font-style:italic}

/* about */
.about{top:1324px;height:698px}
.about h2{left:108px;top:80px;font-size:36px}
.about-copy{left:108px;top:136px;width:491px;font-family:"Open Sans",sans-serif;font-size:14.2px;line-height:25.7px;color:var(--text);text-align:justify}
.about-copy p+p{margin-top:25.7px}
.about .btn{left:108px;top:563px;width:128px;height:42px;font-size:15px}
.about-photo{left:637px;top:85px;width:452px;height:520px;border-radius:12px;background:linear-gradient(180deg,var(--placeholder-a),var(--placeholder-b))}

/* faq */
.faq{top:2022px;height:757px;background:var(--orange)}
.faq h2{left:0;width:1200px;top:75px;text-align:center;font-size:35px;color:var(--white)}
.faq-item{position:absolute;width:463px;height:62px;background:var(--white);border-radius:8px;display:flex;align-items:center;padding-left:23px;font-size:16.5px;color:#444}
.faq-item .plus{position:absolute;right:12px;top:9px;width:44px;height:44px;border-radius:50%;background:var(--orange)}
.faq-more{position:absolute;left:488px;top:625px;width:226px;height:46px;border:2px solid var(--white);border-radius:7px;color:var(--white);font-size:14px;font-weight:600;display:flex;align-items:center;justify-content:center}

/* contact */
.contact{top:2779px;height:611px;background:var(--blue);color:var(--white)}
.map{left:111px;top:93px;width:489px;height:427px;border-radius:14px;background:linear-gradient(160deg,#d6e6d8 0%,#e6ece7 100%)}
.contact h2{left:634px;top:82px;font-size:35px}
.contact-item{position:absolute;left:636px}
.contact-item .icon{position:absolute;left:0;top:0;width:70px;height:70px;border-radius:50%;background:var(--orange);display:flex;align-items:center;justify-content:center}
.contact-item .label{position:absolute;left:88px;top:0;font-size:22px;font-weight:600;white-space:nowrap}
.contact-item .value{position:absolute;left:88px;top:40px;font-size:16.5px;white-space:nowrap}
.follow{left:634px;top:477px;font-size:17px;font-weight:500}
.social{position:absolute;width:50px;height:50px;border-radius:50%;background:var(--blue-2)}
.review{display:flex;align-items:center;gap:8px;font-size:22px;font-weight:700}
.review i{display:block;width:30px;height:30px;border-radius:50%;background:var(--white)}

/* footer */
.site-footer{top:3390px;height:416px;background:var(--white)}
.f-title{left:108px;top:82px;font-size:21px;font-weight:500;line-height:39px}
.f-row{left:108px;font-size:21px;font-weight:500;white-space:nowrap}
.f-row small{font-size:14px;font-weight:600;margin-left:8px}
.f-social{position:absolute;top:250px;width:46px;height:46px;border-radius:50%;background:var(--blue)}
.f-review{left:233px;top:258px;color:var(--ink)}
.f-review i{background:var(--blue-3)}
.subscribe{left:497px;top:88px;width:362px;height:53px;border:1.5px solid #ccc;display:flex;align-items:center;padding:0 18px;justify-content:space-between;font-size:14px;color:#333}
.badge{left:492px;top:179px;width:144px;height:111px;border-radius:50%;background:#eeeeee;border:2px solid #ddd}
.quick{right:111px;top:82px;text-align:right}
.quick h3{font-size:21px;font-weight:500;margin-bottom:8px}
.quick a{display:block;font-size:14.5px;color:#444;text-decoration:none;line-height:30px}
.copyright{left:0;width:1200px;top:360px;text-align:center;font-family:"Open Sans",sans-serif;font-size:15px;color:#444}
</style>
</head>
<body>

<header class="hero">
  <div class="hero-photo" role="img" aria-label="Photo placeholder: river valley landscape at sunrise"></div>
  <div class="abs logo">
    <div class="logo-mark"></div>
    <div class="logo-name">Ashcombe Tube Drift</div>
  </div>
  <nav class="abs nav" style="left:0;top:54px">
    <a class="active" href="#" style="left:664px">HOME</a>
    <a href="#pricing" style="left:748px">PRICING</a>
    <a href="#about" style="left:848px">ABOUT</a>
    <a href="#faq" style="left:940px">FAQ</a>
    <a href="#contact" style="left:1005px">CONTACT</a>
  </nav>
  <h1 class="abs display hero-title">FLOAT THE NORTH<br>SASKATCHEWAN<br>THROUGH DOWNTOWN<br>EDMONTON</h1>
  <a class="btn">Book Now</a>
  <div class="arrow" style="left:553px"><svg width="14" height="14" viewBox="0 0 14 14"><path d="M9 2 4 7l5 5" fill="none" stroke="#222" stroke-width="2"/></svg></div>
  <div class="arrow" style="left:604px"><svg width="14" height="14" viewBox="0 0 14 14"><path d="M5 2l5 5-5 5" fill="none" stroke="#222" stroke-width="2"/></svg></div>
</header>

<section class="pricing" id="pricing">
  <div class="abs pricing-photo" role="img" aria-label="Photo placeholder: snowy mountain river"></div>
  <div class="abs price-badge">Tube and Shuttle<br>$30/person<span>BOOK NOW</span></div>
  <h2 class="abs display">PRICING</h2>
  <p class="abs lead">We keep our pricing simple and include everything you need:</p>
  <ul class="abs includes">
    <li>Premium comfort float tube with backrest and cup holder</li>
    <li>Lifejacket</li>
    <li>Paddle</li>
    <li>Round trip shuttle service</li>
    <li>Safety training</li>
    <li>Staff assistance</li>
    <li>Parking</li>
    <li>Unlimited Fun!</li>
  </ul>
  <a class="abs book-link">BOOK NOW</a>
  <p class="abs group">Group of 10 or more?</p>
  <a class="btn">Contact Us</a>
  <p class="abs note">*does not include taxes or fees</p>
</section>

<section class="about" id="about">
  <h2 class="abs display">ABOUT US</h2>
  <div class="abs about-copy">
    <p>Float the North Saskatchewan through downtown Edmonton Edmonton's Best Summer Activity We provide the lifejacket, paddle, river tube and shuttle service. You just have to show up. Ashcombe Tube Drift was launched to provide people in the Edmonton area a favorite summer activity. Nothing is better on a hot summer day, than spending it on the river and seeing Edmonton from a new perspective.</p>
    <p>Our home base and meeting spot is at Cedar Landing (Map Link), by the Greenhouse Pavilion. This is where you will check in, and board the shuttle. The shuttle will take all floaters up river to Birchwood Park Boat Launch, where your tube will be waiting. Once on the river, you can sit back, relax, explore and enjoy the view. Once you complete the float, and arrive back at Cedar Landing, staff will be available to assist in exiting the river where you will return your tube and gear. Safety is our top priority, but having fun is a close second. Don't miss out on Edmonton's best summer activity.</p>
  </div>
  <a class="btn">Book Now</a>
  <div class="abs about-photo" role="img" aria-label="Photo placeholder: pedestrian bridge and city skyline"></div>
</section>

<section class="faq" id="faq">
  <h2 class="abs display">FAQ</h2>
  <div class="faq-item" style="left:129px;top:143px">How do I reserve my float?<span class="plus"></span></div>
  <div class="faq-item" style="left:609px;top:143px">Where should I park?<span class="plus"></span></div>
  <div class="faq-item" style="left:129px;top:222px">What safety information should I know?<span class="plus"></span></div>
  <div class="faq-item" style="left:609px;top:222px">How long does the trip take?<span class="plus"></span></div>
  <div class="faq-item" style="left:129px;top:301px">What is included?<span class="plus"></span></div>
  <div class="faq-item" style="left:609px;top:301px">What happens if I miss my shuttle?<span class="plus"></span></div>
  <div class="faq-item" style="left:129px;top:380px">What should I bring?<span class="plus"></span></div>
  <div class="faq-item" style="left:609px;top:380px">How do I complete the waiver?<span class="plus"></span></div>
  <div class="faq-item" style="left:129px;top:459px">Where are you located?<span class="plus"></span></div>
  <div class="faq-item" style="left:609px;top:459px">Are lifejackets required?<span class="plus"></span></div>
  <div class="faq-item" style="left:129px;top:538px">What time should I arrive?<span class="plus"></span></div>
  <div class="faq-item" style="left:609px;top:538px">What do I do if there is bad weather on the<span class="plus"></span></div>
  <svg class="abs" style="left:0;top:0" width="1200" height="757" aria-hidden="true">
    <g stroke="#fff" stroke-width="2">
      <path d="M560 165v18M551 174h18"/><path d="M1040 165v18M1031 174h18"/>
      <path d="M560 244v18M551 253h18"/><path d="M1040 244v18M1031 253h18"/>
      <path d="M560 323v18M551 332h18"/><path d="M1040 323v18M1031 332h18"/>
      <path d="M560 402v18M551 411h18"/><path d="M1040 402v18M1031 411h18"/>
      <path d="M560 481v18M551 490h18"/><path d="M1040 481v18M1031 490h18"/>
      <path d="M560 560v18M551 569h18"/><path d="M1040 560v18M1031 569h18"/>
    </g>
  </svg>
  <div class="faq-more">VIEW MORE QUESTIONS?</div>
</section>

<section class="contact" id="contact">
  <div class="abs map" role="img" aria-label="Map placeholder: meeting point location"></div>
  <h2 class="abs display">CONTACT US</h2>
  <div class="contact-item" style="top:142px">
    <div class="icon"><svg width="20" height="26" viewBox="0 0 20 26"><path d="M10 1a8 8 0 0 0-8 8c0 6 8 16 8 16s8-10 8-16a8 8 0 0 0-8-8z" fill="#fff"/><circle cx="10" cy="9" r="3" fill="#F0912C"/></svg></div>
    <div class="label">Address :</div>
    <div class="value">4120 Riverbend Rd NW, Edmonton, AB</div>
  </div>
  <div class="contact-item" style="top:244px">
    <div class="icon"><svg width="22" height="22" viewBox="0 0 24 24"><path d="M6.6 10.8a15 15 0 0 0 6.6 6.6l2.2-2.2a1 1 0 0 1 1-.25 11.4 11.4 0 0 0 3.6.57 1 1 0 0 1 1 1V20a1 1 0 0 1-1 1A17 17 0 0 1 3 4a1 1 0 0 1 1-1h3.5a1 1 0 0 1 1 1c0 1.25.2 2.45.57 3.57a1 1 0 0 1-.25 1z" fill="#fff"/></svg></div>
    <div class="label">Phone :</div>
    <div class="value">+1 555 014 2290</div>
  </div>
  <div class="contact-item" style="top:356px">
    <div class="icon"><svg width="24" height="18" viewBox="0 0 24 18"><rect x="1" y="1" width="22" height="16" rx="2" fill="#fff"/><path d="M1 2l11 8 11-8" fill="none" stroke="#F0912C" stroke-width="2"/></svg></div>
    <div class="label">Email Address :</div>
    <div class="value">info@ashcombetubedrift.com</div>
  </div>
  <p class="abs follow">FOLLOW US :</p>
  <span class="social" style="left:761px;top:465px" aria-label="social profile"></span>
  <span class="social" style="left:820px;top:465px" aria-label="photo profile"></span>
  <div class="abs review" style="left:887px;top:472px"><i></i>TrailReview</div>
</section>

<footer class="site-footer">
  <p class="abs f-title">ASHCOMBE TUBE DRIFT<br>CONNECT</p>
  <p class="abs f-row" style="top:166px">EMAIL:<small>info@ashcombetubedrift.com</small></p>
  <p class="abs f-row" style="top:206px">LOCATION:<small>Cedar Landing</small></p>
  <span class="f-social" style="left:108px" aria-label="social profile"></span>
  <span class="f-social" style="left:168px" aria-label="photo profile"></span>
  <div class="abs review f-review"><i></i>TrailReview</div>
  <div class="abs subscribe">Email Address
    <svg width="16" height="16" viewBox="0 0 16 16"><path d="M15 1 1 7l5 2 2 6z" fill="#F0912C"/></svg>
  </div>
  <div class="abs badge" aria-label="Open every day badge"></div>
  <div class="abs quick">
    <h3>QUICK LINKS</h3>
    <a href="#">HOME</a><a href="#pricing">PRICING</a><a href="#about">ABOUT</a><a href="#faq">FAQ</a><a href="#contact">CONTACT</a>
  </div>
  <p class="abs copyright">© 2022 Company name &nbsp;| All Rights Reserved | Terms and Conditions</p>
</footer>

</body>
</html>
```